Computer Service Provider in Need of New Letterhead Design

We are BrackenLoop Computer Services, a computer/IT services company that provides IT Support, software, hardware, virus monitoring, etc. in Vermont. We are looking for new letterhead, that is both professional and matches the current theme of our business cards & website.
Please note that we want to include the following information:
www.BrackenLoop.example
802-471-3926
742 Hollis Meadow Lane, Williston, VT 05495
Responsive Support • Friendly Experts • Reliable Results
I will be attaching our logo along with the business card images.
We would love to have the

```html
<!DOCTYPE html>
<html lang="en">
<head>
<meta charset="utf-8">
<title>BrackenLoop Computer Services – Letterhead</title>
<link rel="stylesheet" href="https://fonts.googleapis.com/css2?family=Roboto:wght@400;500&display=swap">
<style>
  :root {
    --brand-blue: #1f5a8a;
    --ink-grey: #7b7b7b;
    --ink-dark: #4a4a4a;
    --paper: #ffffff;
    --backdrop: #ececec;
  }
  * { margin: 0; padding: 0; box-sizing: border-box; }
  html, body {
    width: 1200px; height: 866px; overflow: hidden;
    background: var(--backdrop);
    font-family: "Roboto", Arial, sans-serif;
  }
  .letterhead {
    position: absolute; left: 297px; top: 10px;
    width: 605px; height: 846px;
    background: var(--paper);
  }
  .brand {
    position: absolute; left: 53px; top: 53px;
    display: flex; align-items: center; gap: 8px;
  }
  .brand-square { width: 47px; height: 47px; background: var(--brand-blue); }
  .brand-name {
    color: var(--brand-blue); font-size: 17px; font-weight: 500;
    line-height: 1.15; width: 160px;
  }
  .contact {
    position: absolute; left: 435px; top: 48px;
    font-size: 9.5px; color: var(--ink-dark); line-height: 12.5px;
    font-style: normal;
  }
  .contact-address { margin-bottom: 5px; }
  .contact-row { display: flex; align-items: center; gap: 5px; margin-top: 1.5px; }
  .contact-row svg { width: 10px; height: 10px; flex: none; }
  .recipient {
    position: absolute; left: 53px; top: 253px;
    font-size: 11px; line-height: 16px; color: var(--ink-grey);
  }
  .body-text {
    position: absolute; left: 53px; width: 501px;
    font-size: 10.8px; line-height: 15.7px; color: var(--ink-grey);
    text-align: justify;
  }
  .body-text.first { top: 341px; }
  .body-text.second { top: 482px; }
  .signature {
    position: absolute; left: 53px; top: 567px;
    width: 113px; height: 77px;
    background: linear-gradient(90deg, rgba(31,90,138,0.18), rgba(31,90,138,0.06));
  }
  .sign-title {
    position: absolute; left: 52px; top: 656px;
    font-size: 11px; color: var(--ink-grey);
  }
  .tagline {
    position: absolute; left: 0; right: 0; top: 810px;
    text-align: center; font-size: 10.5px; color: var(--ink-dark);
  }
</style>
</head>
<body>
  <main class="letterhead">
    <header>
      <div class="brand">
        <div class="brand-square"></div>
        <div class="brand-name">BrackenLoop Computer Services</div>
      </div>
      <address class="contact">
        <div class="contact-address">742 Hollis Meadow Lane<br>Alder Springs, VT 05688</div>
        <div class="contact-row">
          <svg viewBox="0 0 10 10" aria-hidden="true"><circle cx="5" cy="5" r="5" fill="var(--brand-blue)"/><path d="M3.2 2.6l1 .9-.5.8c.4.8 1 1.4 1.8 1.8l.8-.5.9 1-.6.8C4.6 7.2 2.8 5.4 2.5 3.3z" fill="#fff"/></svg>
          <span>802-471-3926</span>
        </div>
        <div class="contact-row">
          <svg viewBox="0 0 10 10" aria-hidden="true"><circle cx="5" cy="5" r="4.4" fill="none" stroke="var(--brand-blue)" stroke-width="1"/><ellipse cx="5" cy="5" rx="1.9" ry="4.4" fill="none" stroke="var(--brand-blue)" stroke-width="0.8"/><path d="M0.8 5h8.4M1.5 3h7M1.5 7h7" stroke="var(--brand-blue)" stroke-width="0.7"/></svg>
          <span>www.BrackenLoop.example</span>
        </div>
      </address>
    </header>

    <section class="recipient">
      Dear Halverson<br>
      Quillstone Print Corporation<br>
      Department Design
    </section>

    <p class="body-text first">Lorem ipsum dolor sit amet, consectetuer adipiscing elit. Aenean commodo ligula eget dolor. Aenean massa. Cum sociis natoque penatibus et magnis dis parturient montes, nascetur ridiculus mus. Donec quam felis, ultricies nec, pellentesque eu, pretium quis, sem. Nulla consequat massa quis enim. Donec pede justo, fringilla vel, aliquet nec, vulputate eget, arcu. In enim justo, rhoncus ut, imperdiet a, venenatis vitae, justo. Nullam dictum felis eu pede mollis pretium. Integer tincidunt. Cras dapibus. Vivamus elementum semper nisi.Nullam dictum felis eu pede mollis pretium. Integer tincidunt. Cras dapibus. Vivamus elementum semper nisi.felis eu pede mollis pretium. Integer tincidunt. Cras dapibus.</p>

    <p class="body-text second">Quisque rutrum. Aenean imperdiet. Etiam ultricies nisi vel augue. Curabitur ullamcorper ultricies nisi. Nam eget dui. Etiam rhoncus. Maecenas tempus, tellus eget condimentum rhoncus, sem quam semper libero, sit amet adipiscing sem neque sed ipsum.felis pede mollis pretium. I am tincidunt. Cras dapibus.</p>

    <div class="signature" role="img" aria-label="Handwritten signature of the director in blue ink"></div>
    <div class="sign-title">Director/Excecutive Director</div>

    <footer class="tagline">Responsive Support • Friendly Experts • Reliable Results</footer>
  </main>
</body>
</html>
```